Lantern Petals Website v.1 - attract floral shop franchisees

I need a simple information website for my new business. We are a franchisor of flower shops. The overall purpose of the website is to promote the company and the service, especially to potential franchisees and retailers. Only about 4 pages are required including homepage, About, For Supermarkets, For Franchisees, and Contact. No special functions are required except the site will have two separate inquiry forms that must be filled out online and submitted via automated email. Similarly, an email form should be linked from the Contact page. I have a logo and business cards designed by ArtMingle, and I would like the site to have a consistent color scheme and style. The key to design will be to express the joy and love associated with flowers and floral bouquets.
IMPORTANT - I will be exporting the website design to Wordpress CMS in a site hosted by HostNimbus. For smooth integration into WordPress hosted by HostNimbus, the designer should build the site using a WordPress-friendly format. Ideally, they should use HTML, CSS, and PHP. Creating a custom theme or using a page builder that exports to WordPress-compatible files is best. This ensures the site can be easily imported and managed within WordPress.

Target Market(s)

Potential franchisees (existing florists or creative types who might like to own a floral business) and supermarkets who might want us to run their floral department

Industry/Entity Type

Floral retailing

Requirements
Must have
• A brand theme that is beautiful, consistent throughout and builds on the logo design
Nice to have
• Show gender and ethnic diversity in customers and florists. Pictures of happy florists (for franchisees) and pictures of amazing floral department displays (for supermarkets)

```html
<!DOCTYPE html>
<html lang="en">
<head>
<meta charset="utf-8">
<title>Lantern Petals</title>
<link href="https://fonts.googleapis.com/css2?family=Montserrat:wght@400;500;600;700&family=Lato:wght@400;700&display=swap" rel="stylesheet">
<style>
:root{
  --green:#019447;
  --yellow:#efae2e;
  --dark:#1c1c1c;
  --text:#222;
  --white:#fff;
  --hero-dark:#2d2a2c;
}
*{box-sizing:border-box;margin:0;padding:0}
html,body{width:1200px;height:3032px;overflow:hidden}
body{position:relative;background:var(--white);font-family:'Lato',sans-serif;color:var(--text)}
.abs{position:absolute}
.hero-photo{left:0;top:0;width:1200px;height:700px;background:linear-gradient(90deg,#2b2829 0%,#3a3230 35%,#8a6a55 55%,#d9a58a 70%,#e9b48d 85%,#c68d69 100%)}
.nav{left:110px;top:40px;width:976px;height:63px;background:var(--white);border-radius:0 32px 32px 0;display:flex;align-items:center;font-family:'Montserrat',sans-serif;font-size:14px;font-weight:500}
.nav-logo{left:110px;top:0;width:162px;height:137px;background:var(--white);border-radius:0 0 81px 81px;display:flex;align-items:center;justify-content:center;font-family:'Montserrat',sans-serif;font-weight:600;color:var(--yellow);font-size:17px;text-align:center;line-height:1.2}
.nav a{position:absolute;color:var(--dark);text-decoration:none;top:22px}
.btn{display:flex;align-items:center;justify-content:center;border-radius:30px;font-family:'Montserrat',sans-serif;font-weight:700;text-decoration:none}
.quote{right:12px;top:12px;width:144px;height:38px;background:var(--yellow);color:var(--white);font-size:13px;border:2px solid #f6d46e}
.welcome{left:111px;top:198px;color:var(--white);font-family:'Montserrat',sans-serif;font-weight:700;font-size:21px}
.hero-name{left:111px;top:248px;color:var(--white);font-family:'Montserrat',sans-serif;font-weight:500;font-size:74px;line-height:1.05}
.get-started{left:111px;top:476px;width:165px;height:53px;background:var(--white);color:#222;font-size:17px}
h2{font-family:'Montserrat',sans-serif;font-weight:500;font-size:41px;position:absolute;left:0;width:1200px;text-align:center}
.para{position:absolute;left:190px;width:820px;text-align:center;font-size:14.5px;line-height:29px}
.inq-new{left:234px;top:1118px;width:316px;height:53px;background:var(--yellow);color:var(--white);font-size:17px;box-shadow:2px 3px 4px rgba(0,0,0,.2)}
.inq-pro{left:593px;top:1118px;width:374px;height:53px;background:var(--green);color:var(--white);font-size:17px;box-shadow:2px 3px 4px rgba(0,0,0,.2)}
.petal-band{left:0;top:1165px;width:1200px;height:400px;background:linear-gradient(180deg,#fff 0%,#f8e5de 40%,#f1c7b8 70%,#e9b3a3 100%)}
.green-block{left:0;top:1480px;width:1200px;height:672px;background:var(--green)}
.super-text{left:111px;top:1608px;width:482px;color:var(--white);font-size:14.5px;line-height:29px;text-align:justify}
.super-sub{left:110px;top:1790px;color:var(--white);font-family:'Lato',sans-serif;font-weight:700;font-size:20px}
.ticks{left:111px;top:1832px;width:500px;list-style:none;color:var(--white);font-size:14.5px;line-height:29px}
.ticks li{position:relative;padding-left:26px}
.ticks svg{position:absolute;left:0;top:9px}
.read-super{left:111px;top:2020px;width:160px;height:53px;background:var(--yellow);color:var(--white);font-size:17px;box-shadow:2px 3px 4px rgba(0,0,0,.2)}
.arch{left:677px;top:1615px;width:369px;height:461px;border:2px solid var(--white);border-radius:185px 185px 0 0;background:linear-gradient(160deg,#f1b48f 0%,#e8c9c4 30%,#5f9a3c 60%,#f3efe9 80%,#3f6e2f 100%)}
.fran-bg{left:0;top:2152px;width:1200px;height:475px;background:linear-gradient(90deg,#d33a52 0%,#f0e6e8 14%,#f4f2f1 50%,#f0e6e8 86%,#d9364e 100%)}
.read-fran{left:520px;top:2493px;width:160px;height:53px;background:linear-gradient(90deg,var(--yellow),var(--green));color:var(--white);font-size:17px;box-shadow:2px 3px 4px rgba(0,0,0,.2)}
.foot-logo{left:111px;top:2705px;display:flex;align-items:center;gap:12px;font-family:'Montserrat',sans-serif;font-weight:600;font-size:30px;color:var(--yellow)}
.foot-logo .dot{width:54px;height:54px;border-radius:50%;background:var(--yellow)}
.social{top:2853px;width:24px;height:24px;border-radius:50%;background:var(--yellow)}
.foot-col h4{font-family:'Montserrat',sans-serif;font-weight:600;font-size:20px;color:var(--dark);margin-bottom:18px}
.foot-col ul{list-style:none;font-size:14.5px}
.foot-col li{height:34px;display:flex;align-items:flex-start;gap:10px}
.contact-row{display:flex;gap:12px;font-size:14.5px;line-height:27px;margin-bottom:16px}
.contact-row .ic{width:32px;height:32px;border-radius:50%;background:var(--yellow);flex:none;display:flex;align-items:center;justify-content:center}
.rule{left:111px;top:2950px;width:976px;height:1px;background:#bbb}
.copy{left:0;top:2987px;width:1200px;text-align:center;font-family:'Montserrat',sans-serif;font-weight:500;font-size:15px}
</style>
</head>
<body>

<div class="abs hero-photo" role="img" aria-label="Florist shop interior with a bright bouquet of pink, orange and yellow tulips on a wooden table"></div>

<svg class="abs" style="left:0;top:520px" width="1200" height="280" viewBox="0 0 1200 280">
  <path d="M0 60 C160 30 300 90 470 130 C700 180 950 120 1200 0 L1200 280 L0 280 Z" fill="#fff"/>
  <path d="M0 60 C160 30 300 90 470 130 C700 180 950 120 1100 70 C900 150 700 200 470 165 C300 140 150 140 0 180 Z" fill="var(--yellow)"/>
  <path d="M0 265 C100 215 230 180 380 178 C250 170 100 185 0 215 Z" fill="var(--green)"/>
</svg>

<div class="abs nav">
  <a style="left:256px">Home</a>
  <a style="left:328px">About Us</a>
  <a style="left:425px">For Supermarkets</a>
  <a style="left:584px">For Franchisees</a>
  <a style="left:726px">Contact</a>
  <a class="abs btn quote" style="top:12px">Request A Quote</a>
</div>
<div class="abs nav-logo">Lantern<br>Petals</div>

<div class="abs welcome">Welcome to</div>
<div class="abs hero-name">Lantern<br>Petals</div>
<a class="abs btn get-started">Get Started</a>

<h2 style="top:750px">About Lantern-petals</h2>
<p class="para" style="top:822px">Fresh flowers convey beauty and love, and in our view should become something every person regularly enjoys. Lantern Petals is an entrepreneurial company created to make top quality fresh flowers and professionally-designed bouquets accessible to every consumer at affordable prices.</p>
<p class="para" style="top:938px">Professional florists typically sell the finest quality stems, design the most beautiful bouquets and provide the finest customer service, but their costs – of floral products, retail spaces, labor and marketing – force them to pass high prices along to customers. Supermarket flower departments benefit from high customer footfall, economies of scale and low pricing, but their quality of stems and bouquets is typically poor, staffing is limited, and staff turnover is high which can result in inefficiency, wastage, poorly merchandised selections and limited service.</p>
<a class="abs btn inq-new">New Florist Franchise Inquiry</a>
<a class="abs btn inq-pro">Professional Florist Franchise Inquiry</a>

<div class="abs petal-band" role="img" aria-label="Soft pink carnations and blossoms along the lower edge"></div>
<div class="abs green-block"></div>
<svg class="abs" style="left:0;top:1310px" width="1200" height="250" viewBox="0 0 1200 250">
  <path d="M0 250 C250 110 520 60 760 90 C950 115 1080 140 1200 130 L1200 250 Z" fill="var(--green)"/>
  <path d="M110 220 C330 100 600 70 800 110 C950 140 1080 150 1200 140 L1200 190 C1080 200 950 190 800 160 C600 110 330 120 110 220 Z" fill="var(--yellow)"/>
  <path d="M800 75 C950 75 1080 50 1200 0 L1200 45 C1080 70 960 80 800 75 Z" fill="var(--green)"/>
</svg>

<h2 style="top:1513px;color:var(--white)">For Supermarkets</h2>
<p class="abs super-text">Lantern Petals works with some of the country's largest and most progressive supermarkets to provide franchisee ownership and operation of their strategically important floral departments. Supermarkets find that Lantern Petals is able to improve their financial outcomes, provide attentive customer service and satisfaction, and lift the quality of the entire store environment.</p>
<div class="abs super-sub">Opportunity for Supermarkets:</div>
<ul class="abs ticks">
  <li><svg width="14" height="12" viewBox="0 0 14 12"><path d="M1 6 L5 10 L13 1" stroke="#fff" stroke-width="2.6" fill="none"/></svg>Enhance floral revenue streams with efficient assortments and new offerings</li>
  <li><svg width="14" height="12" viewBox="0 0 14 12"><path d="M1 6 L5 10 L13 1" stroke="#fff" stroke-width="2.6" fill="none"/></svg>Reduce the costs of operating a floral department</li>
  <li><svg width="14" height="12" viewBox="0 0 14 12"><path d="M1 6 L5 10 L13 1" stroke="#fff" stroke-width="2.6" fill="none"/></svg>Improve the quality, useful life and merchandising of floral products</li>
  <li><svg width="14" height="12" viewBox="0 0 14 12"><path d="M1 6 L5 10 L13 1" stroke="#fff" stroke-width="2.6" fill="none"/></svg>Provide attentive customer service, including semi-custom bouquets, by professional florist staff</li>
</ul>
<a class="abs btn read-super">Read More</a>
<div class="abs arch" role="img" aria-label="Bouquet of peach roses, green chrysanthemums and white blooms"></div>

<div class="abs fran-bg" role="img" aria-label="Red and pink roses with green sprigs framing a pale background"></div>
<h2 style="top:2213px">For Franchisees</h2>
<p class="para" style="left:175px;width:850px;top:2287px">Lantern Petals brings the best of professional florists and supermarkets together for the benefit of consumers. It supports a national network of owner-operator franchisees, who in many cases are multi-site professional florists, with comprehensive services to enhance franchise profitability.</p>
<p class="para" style="left:175px;width:850px;top:2403px">Lantern Petals works with some of the country's largest and most progressive supermarkets to provide franchisee ownership and operation of their strategically important floral departments.</p>
<a class="abs btn read-fran">Read More</a>

<div class="abs foot-logo"><span class="dot"></span>Lantern Petals</div>
<div class="abs social" style="left:133px"></div>
<div class="abs social" style="left:178px"></div>
<div class="abs social" style="left:224px"></div>
<div class="abs social" style="left:268px"></div>

<div class="abs foot-col" style="left:421px;top:2700px">
  <h4>Quick Links</h4>
  <ul>
    <li><svg width="13" height="12" viewBox="0 0 13 12"><path d="M0 6H11M6 1L11 6L6 11" stroke="var(--yellow)" stroke-width="2" fill="none"/></svg>Home</li>
    <li><svg width="13" height="12" viewBox="0 0 13 12"><path d="M0 6H11M6 1L11 6L6 11" stroke="var(--yellow)" stroke-width="2" fill="none"/></svg>About</li>
    <li><svg width="13" height="12" viewBox="0 0 13 12"><path d="M0 6H11M6 1L11 6L6 11" stroke="var(--yellow)" stroke-width="2" fill="none"/></svg>For Supermarkets</li>
    <li><svg width="13" height="12" viewBox="0 0 13 12"><path d="M0 6H11M6 1L11 6L6 11" stroke="var(--yellow)" stroke-width="2" fill="none"/></svg>For Franchisees</li>
    <li><svg width="13" height="12" viewBox="0 0 13 12"><path d="M0 6H11M6 1L11 6L6 11" stroke="var(--yellow)" stroke-width="2" fill="none"/></svg>Contact Us</li>
  </ul>
</div>
<div class="abs foot-col" style="left:641px;top:2700px">
  <h4>Help Links</h4>
  <ul>
    <li><svg width="13" height="12" viewBox="0 0 13 12"><path d="M0 6H11M6 1L11 6L6 11" stroke="var(--yellow)" stroke-width="2" fill="none"/></svg>FAQ</li>
    <li><svg width="13" height="12" viewBox="0 0 13 12"><path d="M0 6H11M6 1L11 6L6 11" stroke="var(--yellow)" stroke-width="2" fill="none"/></svg>Terms of use</li>
    <li><svg width="13" height="12" viewBox="0 0 13 12"><path d="M0 6H11M6 1L11 6L6 11" stroke="var(--yellow)" stroke-width="2" fill="none"/></svg>Privacy Policy</li>
    <li><svg width="13" height="12" viewBox="0 0 13 12"><path d="M0 6H11M6 1L11 6L6 11" stroke="var(--yellow)" stroke-width="2" fill="none"/></svg>Support Links</li>
    <li><svg width="13" height="12" viewBox="0 0 13 12"><path d="M0 6H11M6 1L11 6L6 11" stroke="var(--yellow)" stroke-width="2" fill="none"/></svg>Conditions</li>
  </ul>
</div>
<div class="abs foot-col" style="left:846px;top:2700px">
  <h4>Contact Us</h4>
  <div class="contact-row"><span class="ic"><svg width="14" height="18" viewBox="0 0 14 18"><path d="M7 17C3 11 1 8.5 1 6.5A6 6 0 0 1 13 6.5C13 8.5 11 11 7 17Z" fill="#fff"/><circle cx="7" cy="6.5" r="2.2" fill="var(--yellow)"/></svg></span><span>Lantern-petals<br>United States</span></div>
  <div class="contact-row"><span class="ic"><svg width="16" height="16" viewBox="0 0 16 16"><path d="M3 1L6 4L4.5 6C5.5 8 8 10.5 10 11.5L12 10L15 13L13 15C7 14.5 1.5 9 1 3Z" fill="#fff"/></svg></span><span>+1.555.014.2276</span></div>
  <div class="contact-row"><span class="ic"><svg width="16" height="12" viewBox="0 0 16 12"><rect x="0.5" y="0.5" width="15" height="11" rx="1.5" fill="#fff"/><path d="M1 1.5L8 7L15 1.5" stroke="var(--yellow)" stroke-width="1.5" fill="none"/></svg></span><span>hello@lanternpetals.example</span></div>
</div>

<div class="abs rule"></div>
<div class="abs copy">Copyrights@2024.Lanternpetals.example.All Rights Reserved</div>

</body>
</html>
```